Dental Practice Billboard Design

We are a newer dental practice in need of a simple but appealing billboard for our growing dental practice to attract new patients. The practice is owned by husband and wife dentists and is family friendly in a small town in Kentucky. We try to be very friendly and caring to our patients. Would prefer a blue background for the billboard and our tooth logo to be prominent. We are partial to the Patua One font used in the image below but please feel free to tweak it as you deem necessary. The shape of the uppercase D and lowercase g are why we like that font, so fonts with a similarly shaped “D” and “g” would work as well. Please include our phone number (555) 847-1390. Please see our website Harlowbrookdentistry.example for more info on the practice if needed. Thank you! Looking forward to seeing your creation.
Updates

The dimensions will be 12ft x 24ft (3.6576m x 7.3152m). Apologies for not including this in the original prompt. Thank you all for your submissions.

Industry/Entity Type

Dental

Font styles to use
Other font styles liked:
• Patua One

Colors
0054AA
0677BA
7BADD7
CADEEF
E8F1F8
0094D4
00A9DD
6FCCEA
C7EBF8
E9F6FB
00AB8E
00BBA5
67D7C9
C6EFE9
E9F9F6
59FF00
82FF00
B8FF75
E3FFCB
F4FFEA

Requirements
Must have
• Phone number, website, Logo, Practice name “Harlow Brook Dentistry”
Should not have
• A tagline or slogan

```html
<!DOCTYPE html>
<html lang="en">
<head>
<meta charset="UTF-8">
<title>Harlow Brook Dentistry Billboard</title>
<link href="https://fonts.googleapis.com/css2?family=Bitter:wght@600;700&family=Open+Sans:wght@600&display=swap" rel="stylesheet">
<style>
  :root {
    --page-bg: #5a5a5a;
    --sky-top: #c9e6fa;
    --sky-bottom: #eef8fe;
    --brand-blue: #1652b3;
    --deep-blue: #0f4aa3;
    --brand-green: #17a317;
    --tick-green: #1fae2a;
    --ink: #2a2a2a;
    --white: #ffffff;
  }
  * { margin: 0; padding: 0; box-sizing: border-box; }
  html, body { width: 924px; height: 1200px; overflow: hidden; background: var(--page-bg); }
  .billboard {
    position: absolute; left: 22px; top: 471px; width: 880px; height: 257px;
    background: linear-gradient(180deg, var(--sky-top), var(--sky-bottom));
    overflow: hidden; font-family: "Bitter", Georgia, serif;
  }
  .contact-band { position: absolute; left: 0; top: 208px; width: 880px; height: 49px; }
  .team-photo {
    position: absolute; left: 0; top: 0; width: 232px; height: 257px;
    background: linear-gradient(135deg, #1d5cbc 0%, #dfe9f2 35%, #f4f6f8 60%, #22a82a 100%);
    border-radius: 0 120px 120px 0 / 0 60% 60% 0;
  }
  .practice-name {
    position: absolute; left: 240px; top: 14px; width: 640px; height: 70px;
    display: flex; align-items: center; justify-content: center; gap: 14px;
    color: var(--brand-blue); font-weight: 700; font-size: 44px; line-height: 1; white-space: nowrap;
  }
  .practice-name .mark { width: 30px; height: 30px; border-radius: 50%; background: var(--brand-green); flex: none; }
  .services-pill {
    position: absolute; left: 448px; top: 96px; width: 224px; height: 22px;
    background: var(--deep-blue); color: var(--white); border-radius: 6px;
    font-weight: 600; font-size: 13px; letter-spacing: 0.4px;
    display: flex; align-items: center; justify-content: center;
  }
  .service-list { position: absolute; top: 127px; list-style: none; color: var(--ink); font-weight: 600; font-size: 15.5px; }
  .service-list li { height: 22.5px; display: flex; align-items: center; gap: 8px; white-space: nowrap; }
  .service-list li::before {
    content: "✓"; width: 9px; height: 9px; border-radius: 50%; background: var(--tick-green);
    color: var(--white); font-size: 7px; line-height: 9px; text-align: center; font-family: sans-serif; flex: none;
  }
  .col-1 { left: 266px; } .col-2 { left: 408px; } .col-3 { left: 576px; } .col-4 { left: 703px; }
  .phone {
    position: absolute; left: 232px; top: 208px; height: 49px; display: flex; align-items: center; gap: 6px;
    color: var(--white); font-family: "Open Sans", Arial, sans-serif; font-weight: 600; font-size: 22px;
  }
  .website {
    position: absolute; left: 470px; top: 208px; width: 402px; height: 49px; display: flex; align-items: center; justify-content: center;
    color: var(--white); font-weight: 700; font-size: 20px; white-space: nowrap;
  }
</style>
</head>
<body>
  <div class="billboard">
    <svg class="contact-band" viewBox="0 0 880 49" aria-hidden="true">
      <defs>
        <linearGradient id="bandBlue" x1="0" x2="1">
          <stop offset="0" stop-color="#0f3f95"/><stop offset="1" stop-color="#1d6cc0"/>
        </linearGradient>
      </defs>
      <polygon points="180,0 480,0 465,49 180,49" fill="url(#bandBlue)"/>
      <polygon points="480,0 880,0 880,49 465,49" fill="#17a317"/>
    </svg>

    <div class="team-photo" role="img" aria-label="Photo of the two dentists in white coats, smiling, framed by blue and green curves"></div>

    <h1 class="practice-name"><span class="mark"></span><span>Harlow Brook Dentistry</span></h1>

    <div class="services-pill">SERVICES FOR YOUR SMILE</div>

    <ul class="service-list col-1"><li>Crowns</li><li>Root Canals</li><li>Extractions</li></ul>
    <ul class="service-list col-2"><li>Clear Aligners</li><li>Veneers</li><li>Bridges</li></ul>
    <ul class="service-list col-3"><li>Fillings</li><li>Whitening</li><li>Implants</li></ul>
    <ul class="service-list col-4"><li>Cleanings</li><li>Dentures</li><li>Overdentures</li></ul>

    <div class="phone">
      <svg width="20" height="20" viewBox="0 0 20 20" aria-hidden="true">
        <circle cx="10" cy="10" r="10" fill="#1fae2a"/>
        <path d="M6.5 5.5c.6-.6 1.2-.5 1.5 0l1 1.6c.3.5.2 1-.2 1.3l-.6.5c.5 1.1 1.4 2 2.5 2.5l.5-.6c.3-.4.8-.5 1.3-.2l1.6 1c.5.3.6.9 0 1.5-.8.8-2 1.1-3.3.5-2-1-3.6-2.6-4.6-4.6-.6-1.3-.3-2.5.3-3.5z" fill="#fff"/>
      </svg>
      (555) 847-1390
    </div>
    <div class="website">www.harlowbrookdentistry.example</div>
  </div>
</body>
</html>
```